Business cards and stationary design

We just completed the design of our new logo and we need to print new business cards and letterhead for our nonprofit. We are looking for a fresh new design that shows off our new logo. On letterhead, we must have a column on the right or left to include our Board of Directors (up to 45 names) (see attachment)

Industry/Entity Type

Non-Profit

Contact Information for Business Card

Standard business card with name, title, Company name, mailing address phone numbers, email address and website. Tagline on back "Bringing the homeless home"

Font styles to use
Sans Serif

Requirements
Must have
• include pertinent information above
• new logo
• fonts compatible with logo
• should use logo colors only
Nice to have
• tag lines

```html
<!DOCTYPE html>
<html lang="en">
<head>
<meta charset="utf-8">
<title>Harbor Home Center – Business Card</title>
<link rel="stylesheet" href="https://fonts.googleapis.com/css2?family=Saira:wght@400;600&display=swap">
<style>
  :root {
    --backdrop: #e4e4e4;
    --teal: #0a84a6;
    --sun: #f5b921;
    --paper: #f8f8f8;
    --red: #d61f26;
    --white: #ffffff;
  }
  * { margin: 0; padding: 0; box-sizing: border-box; }
  html, body {
    width: 1200px; height: 582px; overflow: hidden;
    background: var(--backdrop);
    font-family: "Saira", sans-serif;
  }
  .canvas { position: relative; width: 1200px; height: 582px; }
  .card {
    position: absolute; top: 158px;
    width: 464px; height: 264px; overflow: hidden;
  }
  .card-front { left: 122px; background: var(--paper); }
  .card-back { left: 602px; background: var(--red); }

  .front-shape { position: absolute; inset: 0; }

  .contact { position: absolute; left: 30px; top: 62px; color: var(--white); }
  .contact-name {
    font-weight: 600; font-size: 17px; letter-spacing: 1.6px;
    color: var(--sun); line-height: 1;
  }
  .contact-title {
    font-size: 10px; letter-spacing: 1.4px; margin-top: 3px; line-height: 1;
  }
  .contact-address {
    font-size: 10.5px; line-height: 13px; margin-top: 12px;
  }
  .contact-lines { list-style: none; margin-top: 10px; font-size: 10.5px; }
  .contact-lines li { display: flex; align-items: center; height: 15px; }
  .contact-lines li:first-child { font-size: 11.5px; }
  .contact-icon { width: 9px; height: 9px; margin-right: 7px; flex: none; }

  .front-brand {
    position: absolute; left: 246px; top: 118px; width: 200px;
    text-align: center; color: var(--teal);
    font-weight: 600; font-size: 15px; letter-spacing: 1.4px; line-height: 1;
  }

  .back-brand {
    position: absolute; left: 0; right: 0; top: 96px;
    display: flex; align-items: center; justify-content: center; gap: 12px;
    color: var(--white); font-weight: 600; font-size: 26px; letter-spacing: 2px;
  }
  .back-brand-square { width: 18px; height: 18px; background: var(--white); }
  .back-url {
    position: absolute; left: 0; right: 0; top: 222px; text-align: center;
    color: var(--white); font-size: 10px; letter-spacing: 3.6px;
  }
</style>
</head>
<body>
<main class="canvas">
  <section class="card card-front">
    <svg class="front-shape" width="464" height="264" viewBox="0 0 464 264" aria-hidden="true">
      <polygon points="0,0 306,0 178,132 313,264 0,264" fill="var(--teal)"/>
      <polyline points="318,0 190,132 324,264" fill="none" stroke="var(--sun)" stroke-width="4"/>
    </svg>

    <div class="contact">
      <p class="contact-name">DANIEL REYES</p>
      <p class="contact-title">CEO/FOUNDER</p>
      <p class="contact-address">Harbor Home Center<br>4120 Alder Court<br>Fairview, Oregon 97024</p>
      <ul class="contact-lines">
        <li>
          <svg class="contact-icon" viewBox="0 0 10 10" aria-hidden="true"><path d="M2 0.5 L4 2.8 L3 4 Q4.2 6 6 7 L7.2 6 L9.5 8 L8 9.5 Q3.5 9 0.5 2 Z" fill="var(--sun)"/></svg>
          503 555 0147
        </li>
        <li>
          <svg class="contact-icon" viewBox="0 0 10 10" aria-hidden="true"><rect x="0" y="2" width="10" height="6.5" fill="var(--sun)"/><polyline points="0.5,2.5 5,6 9.5,2.5" fill="none" stroke="var(--teal)" stroke-width="1"/></svg>
          daniel@harborhomecenter.org
        </li>
        <li>
          <svg class="contact-icon" viewBox="0 0 10 10" aria-hidden="true"><circle cx="5" cy="5" r="4.8" fill="var(--sun)"/><path d="M5 0.5 V9.5 M0.5 5 H9.5" stroke="var(--teal)" stroke-width="0.8"/></svg>
          www.harborhomecenter.org
        </li>
      </ul>
    </div>

    <p class="front-brand">HARBOR HOME CENTER</p>
  </section>

  <section class="card card-back">
    <p class="back-brand"><span class="back-brand-square"></span>HARBOR HOME CENTER</p>
    <p class="back-url">WWW.HARBORHOMECENTER.ORG</p>
  </section>
</main>
</body>
</html>
```